Tall Fern Roofing Business Card

Need a business card with the logo that was designed here

Contact Information for Business Card

Name, Title, Phone, Email, Website, Company name

```html
<!DOCTYPE html>
<html lang="en">
<head>
<meta charset="UTF-8">
<title>Tall Fern Roofing – Business Card</title>
<link rel="stylesheet" href="https://fonts.googleapis.com/css2?family=Poppins:wght@400;600&display=swap">
<style>
  :root {
    --backdrop: #b7b7b7;
    --brand-blue: #1f77bd;
    --white: #ffffff;
    --roof-grey: #8e9093;
    --rule-light: rgba(255,255,255,0.55);
  }
  * { box-sizing: border-box; margin: 0; padding: 0; }
  html, body {
    width: 1200px; height: 1200px; overflow: hidden;
    background: var(--backdrop);
    font-family: "Poppins", sans-serif;
  }
  .card {
    position: absolute; top: 303px;
    width: 369px; height: 594px;
    overflow: hidden;
  }
  .card--front { left: 200px; background: var(--brand-blue); }
  .card--back { left: 599px; width: 364px; background: var(--white); }

  .wordmark {
    position: absolute; left: 0; right: 0;
    text-align: center; font-weight: 600; line-height: 1;
  }
  .wordmark__name { display: block; font-size: 42px; letter-spacing: 0.5px; }
  .wordmark__sub { display: block; font-size: 17px; letter-spacing: 9px; margin-top: 10px; padding-left: 9px; }
  .card--front .wordmark { top: 420px; color: var(--white); }
  .card--back .wordmark { top: 128px; color: var(--brand-blue); }

  .back-band {
    position: absolute; left: 0; right: 0; top: 355px; bottom: 0;
    background: var(--brand-blue);
    border-top: 3px solid var(--roof-grey);
  }
  .contact {
    position: absolute; left: 0; right: 0; top: 405px;
    text-align: center; color: var(--white);
  }
  .contact__name { font-weight: 600; font-size: 25px; letter-spacing: 0.3px; line-height: 1.1; }
  .contact__title { font-weight: 400; font-size: 16px; line-height: 1.3; }
  .contact__icons {
    display: flex; justify-content: center; align-items: center; gap: 4px;
    margin-top: 14px;
  }
  .contact__rule { width: 52px; height: 1px; background: var(--rule-light); margin: 0 8px; }
  .icon {
    width: 25px; height: 25px; background: var(--white); border-radius: 3px;
    display: flex; align-items: center; justify-content: center;
  }
  .icon svg { width: 16px; height: 16px; }
  .contact__lines { margin-top: 8px; font-size: 17px; line-height: 21px; letter-spacing: 0.2px; }
</style>
</head>
<body>
  <section class="card card--front" aria-label="Card front">
    <div class="wordmark">
      <span class="wordmark__name">Tall Fern</span>
      <span class="wordmark__sub">ROOFING</span>
    </div>
  </section>

  <section class="card card--back" aria-label="Card back">
    <div class="wordmark">
      <span class="wordmark__name">Tall Fern</span>
      <span class="wordmark__sub">ROOFING</span>
    </div>
    <div class="back-band"></div>
    <div class="contact">
      <p class="contact__name">DANIEL CARTER</p>
      <p class="contact__title">Managing Director</p>
      <div class="contact__icons">
        <span class="contact__rule"></span>
        <span class="icon" aria-label="Phone">
          <svg viewBox="0 0 16 16"><path fill="#1f77bd" d="M2 5c0-2 2-3 6-3s6 1 6 3v1h-3V5H5v1H2zM4 7h8l2 6H2z"/><rect x="7" y="9" width="2" height="2" fill="#fff"/></svg>
        </span>
        <span class="icon" aria-label="Email">
          <svg viewBox="0 0 16 16"><rect x="1.5" y="3.5" width="13" height="9" fill="none" stroke="#1f77bd" stroke-width="1.3"/><path d="M1.5 3.5 8 9l6.5-5.5" fill="none" stroke="#1f77bd" stroke-width="1.3"/></svg>
        </span>
        <span class="icon" aria-label="Website">
          <svg viewBox="0 0 16 16"><circle cx="8" cy="8" r="6.5" fill="#1f77bd"/><path d="M4 6c2-1 3 1 4 0s1 3-1 3-2 2-3 1zM10 10c1-1 2 0 2 1l-2 1z" fill="#fff"/></svg>
        </span>
        <span class="contact__rule"></span>
      </div>
      <div class="contact__lines">
        <p>044-987 654 321</p>
        <p>hello@tallfern.com</p>
        <p>www.tallfernroofing.com</p>
      </div>
    </div>
  </section>
</body>
</html>
```